Association qui souhaite améliorer l'accès aux personnes en situation de handicap

Nous sommes une association qui a pour objectif d'améliorer l'accessibilité, augmenter l'offre des activités réalisables dans notre région touristique.
Nous souhaitons réaliser un site internet afin de pouvoir communiquer sur notre association. Nous avons déjà conçu notre flyer sur Plumotrix. Nous souhaiterions une base graphique se rapportant à celui-ci. C'est possible de tout retravailler mais nous souhaitons tout de même retrouver la charte graphique ou code couleur du flyer.
Il nous faudrait quelques pages:
- 1 page : Acceuil / Présentation (Home), Il y aurait le descriptif de l'association, avec ses objectifs à +/- moyen terme
- 1 page : Nos réalisations, celle-ci présenterait les éléments que nous avons réalisés avec des zones de textes et des images classées chronologiquement au fur et à mesure des nouveautés
- 1 page : Media, comme la précédente, mais ou on pourrait voir ou lire sur les divers médias qui parlent de nous
- 1 page : Evenements : c'est une page pour présenter divers activités que nous allons organiser
- 1 page : Contact qui indique comment nous contacter et avec la présentation des 5 ou 6 membres du comité
- 1 link donate : qui arrive sur un formulaire de donnée que l'on pourra faire évoluer sur un système de payement par la suite. Cette bannière doit se retrouver sur toutes les pages
Il est nécessaire que se design puisse être transféré sur une lecture sur téléphone mobile
Personnes en situation de handicap
Associatif

```html
<!DOCTYPE html>
<html lang="en">
<head>
<meta charset="utf-8">
<title>Media – Openway Association</title>
<link rel="stylesheet" href="https://fonts.googleapis.com/css2?family=Raleway:wght@500;600;700;800&family=Mulish:wght@400;600;700&family=Oswald:wght@500&display=swap">
<style>
:root{
  --red:#c01a29;
  --red-bright:#e3202f;
  --ink:#1d1d1d;
  --text:#2b2b2b;
  --muted-bg:#f4f1f1;
  --footer:#262d31;
  --white:#ffffff;
  --caption:rgba(15,15,15,.85);
}
*{box-sizing:border-box;margin:0;padding:0}
html,body{width:1200px;height:2487px;overflow:hidden}
body{position:relative;font-family:"Mulish",sans-serif;color:var(--text);background:var(--white)}
.abs{position:absolute}
.wrap{left:130px;width:940px}

.topbar{top:0;left:0;width:1200px;height:28px;background:var(--red);color:var(--white);font-size:11px}
.topbar .social{position:absolute;left:130px;top:9px;width:9px;height:9px;border-radius:50%;background:var(--white)}
.topbar .mail{position:absolute;right:130px;top:7px;display:flex;align-items:center;gap:6px}

.header{top:28px;left:0;width:1200px;height:62px;background:var(--white);border-bottom:1px solid #e6e6e6}
.brand{position:absolute;left:130px;top:19px;display:flex;align-items:center;gap:8px;font-family:"Raleway",sans-serif;font-weight:700;font-size:14px;line-height:1;color:var(--ink);letter-spacing:.3px}
.brand .mark{width:22px;height:22px;background:var(--red)}
.nav{position:absolute;left:538px;top:0;height:62px;display:flex;align-items:center;gap:40px;font-size:11.5px;color:var(--ink);font-weight:600}
.nav .active{color:var(--red);position:relative}
.nav .active svg{position:absolute;left:1px;top:15px}
.donate{position:absolute;left:976px;top:16px;width:94px;height:30px;border-radius:15px;background:var(--red);color:var(--white);font-size:11.5px;font-weight:700;display:flex;align-items:center;justify-content:center}

.hero{top:90px;left:0;width:1200px;height:272px;background:linear-gradient(180deg,#3d4a3a 0%,#2f3b2a 45%,#384327 75%,#2a3022 100%)}
.hero-title{top:103px;left:0;width:1200px;text-align:center;font-family:"Raleway",sans-serif;font-weight:800;font-size:34px;color:var(--red-bright);letter-spacing:.5px}
.crumbs{top:152px;left:0;width:1200px;text-align:center;font-size:10px;color:#dcdcdc}
.crumbs b{color:var(--white);font-weight:600}

.section-title{left:0;width:1200px;text-align:center;font-family:"Raleway",sans-serif;font-weight:600;font-size:34px;color:var(--ink)}
.lead{text-align:center;font-size:13.5px;line-height:19px;color:var(--ink)}

.grid{display:grid;grid-template-columns:repeat(3,300px);gap:22px 20px}
.card{position:relative;height:290px;overflow:hidden}
.card .photo{position:absolute;inset:0}
.card .cap{position:absolute;left:0;bottom:0;width:100%;height:68px;background:var(--caption);color:var(--white);padding:16px 19px 0}
.cap small,.feature small{display:block;font-size:9.5px;margin-bottom:5px}
.cap h3{font-family:"Raleway",sans-serif;font-weight:600;font-size:15.5px}
.feature{position:absolute;inset:0;background:rgba(196,26,40,.93);color:var(--white);padding:46px 16px 0}
.feature h3{font-family:"Raleway",sans-serif;font-weight:600;font-size:17px;margin:6px 0 24px}
.feature p{font-size:10.5px;line-height:19.3px}

.see-more{top:1216px;left:0;width:1200px;text-align:center;font-size:16px;letter-spacing:3px;color:var(--red)}

.subscribe{top:1276px;left:0;width:1200px;height:265px;background:var(--muted-bg)}
.pill{display:flex;align-items:center;justify-content:center;background:var(--red);color:var(--white);font-size:10.5px;font-weight:600;border-radius:20px;height:39px}

.actions{display:grid;grid-template-columns:repeat(3,300px);gap:20px}
.action .photo{height:199px}
.action h3{font-family:"Raleway",sans-serif;font-weight:500;font-size:17px;color:var(--ink);margin:23px 0 9px}
.action p{font-size:12px;line-height:19px;color:var(--ink)}
.action .pill{width:118px;margin-top:15px}

.footer-shape{top:2027px;left:0;width:1200px;height:460px}
.footer{color:var(--white)}
.f-brand{top:2195px;left:130px;display:flex;align-items:center;gap:8px;font-family:"Raleway",sans-serif;font-weight:700;font-size:15px;color:var(--white)}
.f-brand .mark{width:26px;height:26px;border:2px solid var(--white)}
.f-about{top:2264px;left:130px;width:210px;font-size:10.5px;line-height:16px;color:#e4e4e4}
.f-social{top:2326px;left:130px;width:22px;height:22px;border-radius:50%;background:var(--red)}
.f-col h4{font-family:"Oswald",sans-serif;font-weight:500;font-size:17px;color:var(--red-bright);margin-bottom:12px;letter-spacing:.3px}
.f-col li{list-style:none;font-size:10.5px;color:#e8e8e8;height:22.7px}
.f-contact{display:flex;gap:8px;font-size:10.5px;line-height:13px;color:#e8e8e8;margin-bottom:12px}
.f-contact .ico{flex:none;width:22px;height:22px;border-radius:50%;border:1px solid #7a7f82;display:flex;align-items:center;justify-content:center}
.f-rule{top:2396px;left:130px;width:940px;border-top:1px dashed #444c50}
.copy{top:2420px;left:0;width:1200px;text-align:center;font-size:10px;color:#e8e8e8}
.copy span{color:var(--red-bright)}
</style>
</head>
<body>

<div class="abs topbar">
  <span class="social"></span>
  <div class="mail">
    <svg width="11" height="8" viewBox="0 0 11 8"><rect x=".5" y=".5" width="10" height="7" fill="none" stroke="#fff"/><path d="M.5 .5l5 4 5-4" fill="none" stroke="#fff"/></svg>
    info@openway-association.ch
  </div>
</div>

<header class="abs header">
  <div class="brand"><span class="mark"></span>OPENWAY ASSOCIATION</div>
  <nav class="nav">
    <span>Home</span>
    <span>Our Achievements</span>
    <span class="active">Media
      <svg width="32" height="8" viewBox="0 0 32 8"><polyline points="0,1 5,6 10,1 16,6 21,1 26,6 31,1" fill="none" stroke="#c01a29" stroke-width="1.5"/></svg>
    </span>
    <span>Events</span>
    <span>Contacts</span>
  </nav>
  <div class="donate">DONATE</div>
</header>

<section class="abs hero" role="img" aria-label="Smiling boy in a wheelchair in a flower garden"></section>
<h1 class="abs hero-title" style="top:193px">MEDIA</h1>
<div class="abs crumbs" style="top:241px">Home | <b>Media</b></div>

<h2 class="abs section-title" style="top:420px">Press Releases</h2>
<p class="abs wrap lead" style="top:474px">Sed ut perspiciatis unde omnis iste natus error sit voluptatem accusantium doloremque laudantium, totam rem aperiam, eaque ipsa quae ab illo inventore veritatis et quasi architecto beatae vitae dicta sunt explicabo.</p>

<div class="abs wrap grid" style="top:573px">
  <article class="card">
    <div class="photo" role="img" aria-label="People seated in wheelchairs" style="background:linear-gradient(135deg,#d6403a,#9c1e24)"></div>
    <div class="feature">
      <small>12th July, 2022</small>
      <h3>Accusantium Doloremque</h3>
      <p>Sed ut perspiciatis unde omnis iste natus error sit voluptatem accusantium doloremque laudantium, totam rem aperiam, eaque ipsa quae ab illo inventore veritatis et quasi architecto beatae vitae dicta sunt explicabo. Nemo enim ipsam voluptatem quia voluptas sit aspernatur aut odit aut fugit sed quia consequuntur magni.</p>
    </div>
  </article>
  <article class="card">
    <div class="photo" role="img" aria-label="Family helping a woman through the snow" style="background:linear-gradient(160deg,#e9ecef,#b9c1c8 60%,#5a6670)"></div>
    <div class="cap"><small>12th July, 2022</small><h3>Neque Porro Quisquam</h3></div>
  </article>
  <article class="card">
    <div class="photo" role="img" aria-label="Doctor examining an elderly man's ear" style="background:linear-gradient(160deg,#d9cfb6,#b9a98a 60%,#6f6a63)"></div>
    <div class="cap"><small>12th July, 2022</small><h3>Neque Porro Quisquam</h3></div>
  </article>
  <article class="card">
    <div class="photo" role="img" aria-label="Man in a wheelchair among palm leaves" style="background:linear-gradient(160deg,#b79a3c,#6e7a2c 55%,#3e4a26)"></div>
    <div class="cap"><small>12th July, 2022</small><h3>Neque Porro Quisquam</h3></div>
  </article>
  <article class="card">
    <div class="photo" role="img" aria-label="Therapist fitting a prosthetic arm for a wheelchair user" style="background:linear-gradient(160deg,#d8dbdc,#9ea4a8 55%,#3b4048)"></div>
    <div class="cap"><small>12th July, 2022</small><h3>Neque Porro Quisquam</h3></div>
  </article>
  <article class="card">
    <div class="photo" role="img" aria-label="Woman pushing a wheelchair outdoors under a cloudy sky" style="background:linear-gradient(180deg,#8a96a3,#5b6672 55%,#3f4a38)"></div>
    <div class="cap"><small>12th July, 2022</small><h3>Neque Porro Quisquam</h3></div>
  </article>
</div>

<div class="abs see-more">SEE MORE</div>

<section class="abs subscribe"></section>
<h2 class="abs section-title" style="top:1340px">Receive our Press Releases</h2>
<p class="abs lead" style="top:1393px;left:0;width:1242px">Subscribe to our press releases and stay informed</p>
<div class="abs pill" style="top:1431px;left:563px;width:117px">SUBSCRIBE</div>

<h2 class="abs section-title" style="top:1588px">Our Actions</h2>
<div class="abs wrap actions" style="top:1657px">
  <article class="action">
    <div class="photo" role="img" aria-label="Parents embracing their son outdoors" style="background:linear-gradient(135deg,#3f5a2c,#6c7f4a 50%,#2a3424)"></div>
    <h3>Child Protection</h3>
    <p>Lorem<br>Ipsum dolor<br>Sit amet</p>
    <div class="pill">LEARN MORE</div>
  </article>
  <article class="action">
    <div class="photo" role="img" aria-label="Toddler sitting on a park bench" style="background:linear-gradient(135deg,#8fa3a5,#b99b7d 50%,#6f6a58)"></div>
    <h3>Child Health</h3>
    <p>Lorem<br>Ipsum dolor<br>Sit amet</p>
    <div class="pill">LEARN MORE</div>
  </article>
  <article class="action">
    <div class="photo" role="img" aria-label="Two children playing with a board game in a classroom" style="background:linear-gradient(135deg,#d7c5b0,#c9a78d 50%,#8aa07a)"></div>
    <h3>Children in Humanitarian Crises</h3>
    <p>Lorem<br>Ipsum dolor<br>Sit amet</p>
    <div class="pill">LEARN MORE</div>
  </article>
</div>

<svg class="abs footer-shape" width="1200" height="460" viewBox="0 0 1200 460" aria-hidden="true">
  <polygon points="0,53 471,125 1200,0 1200,460 0,460" fill="#262d31"/>
</svg>

<footer class="footer">
  <div class="abs f-brand"><span class="mark"></span>OPENWAY ASSOCIATION</div>
  <p class="abs f-about">Sed ut perspiciatis unde omnis iste natus error sit voluptatem accusantium rem aperiam</p>
  <span class="abs f-social"></span>

  <div class="abs f-col" style="top:2190px;left:450px">
    <h4>SITEMAP</h4>
    <ul><li>Home</li><li>Our Achivements</li><li>Media</li><li>Events</li><li>Contact Us</li></ul>
  </div>
  <div class="abs f-col" style="top:2190px;left:670px">
    <h4>OTHERS</h4>
    <ul><li>Privacy Policy</li><li>Terms &amp; Conditions</li><li>Leagal</li><li>Donate</li><li>Help / Support</li></ul>
  </div>
  <div class="abs f-col" style="top:2190px;left:875px;width:200px">
    <h4>CONTACTS</h4>
    <div class="f-contact">
      <span class="ico"><svg width="8" height="11" viewBox="0 0 8 11"><path d="M4 10.5C1.5 7 .5 5.5.5 4a3.5 3.5 0 0 1 7 0c0 1.5-1 3-3.5 6.5z" fill="none" stroke="#e3202f"/><circle cx="4" cy="4" r="1.2" fill="#e3202f"/></svg></span>
      <span style="padding-top:2px">Chemin des Erables 12 / 1870<br>Montvert</span>
    </div>
    <div class="f-contact">
      <span class="ico"><svg width="11" height="8" viewBox="0 0 11 8"><rect x=".5" y=".5" width="10" height="7" fill="#e3202f"/><path d="M.5 .5l5 4 5-4" fill="none" stroke="#262d31"/></svg></span>
      <span style="padding-top:5px">info@openway-association.ch</span>
    </div>
  </div>

  <div class="abs f-rule"></div>
  <p class="abs copy">Copyright © 2022 <span>Openway Association</span>. All Rights Reserved.</p>
</footer>

</body>
</html>
```